Lumavento business card

We need a modern business card - With our 4 colors - See web: www.lumavento.dk

I have attached logo and som old business Cards we have - Lets Make the new ones shine...:-) -

Industry/Entity Type

Business

Requirements
Must have
• the logo with lumavento only,

```html
<!DOCTYPE html>
<html lang="da">
<head>
<meta charset="utf-8">
<title>Lumavento – visitkort</title>
<link rel="stylesheet" href="https://fonts.googleapis.com/css2?family=Arimo:wght@400;700&display=swap">
<style>
  :root {
    --backdrop: #e4e4e2;
    --card: #ffffff;
    --lime: #8cc63f;
    --lime-soft: #9fd055;
    --lime-line: #8cc63f;
    --ink: #3a3a3a;
    --white: #ffffff;
  }
  * { margin: 0; padding: 0; box-sizing: border-box; }
  html, body {
    width: 1200px; height: 950px; overflow: hidden;
    background: var(--backdrop);
    font-family: "Arimo", Arial, sans-serif;
  }
  .canvas { position: relative; width: 1200px; height: 950px; }

  .card {
    position: absolute;
    width: 740px; height: 410px;
    background: var(--card);
    overflow: hidden;
    box-shadow: 0 6px 18px rgba(0,0,0,.18);
  }
  .card--front { left: 80px; top: 50px; }
  .card--back  { left: 380px; top: 490px; }

  /* brand block */
  .brand { position: absolute; width: 300px; text-align: center; }
  .brand__name {
    display: flex; align-items: center; justify-content: center; gap: 12px;
    font-size: 30px; letter-spacing: 3px; color: var(--ink);
    padding-bottom: 10px;
  }
  .brand__dot { width: 24px; height: 24px; border-radius: 50%; background: var(--lime); }
  .brand__rule { height: 2px; background: var(--lime-line); }
  .brand__tagline { margin-top: 12px; font-size: 15px; color: var(--ink); }

  .card--front .brand { left: 220px; top: 160px; }
  .card--back .brand  { left: 410px; top: 150px; }

  /* back side lime field */
  .lime-field {
    position: absolute; left: -380px; top: 0;
    width: 900px; height: 410px;
    background: var(--lime-soft);
    clip-path: ellipse(55% 95% at 35% 100%);
  }

  .contact {
    position: absolute; left: 40px; top: 150px;
    color: var(--white);
  }
  .contact__name { font-size: 22px; font-weight: 700; }
  .contact__role { font-size: 15px; margin-top: 4px; }
  .contact__address { font-size: 15px; margin-top: 22px; line-height: 1.35; }
  .contact__list { list-style: none; margin-top: 12px; font-size: 15px; }
  .contact__list li { display: flex; align-items: center; gap: 10px; line-height: 1.5; }
  .contact__list svg { width: 14px; height: 14px; fill: var(--white); }
</style>
</head>
<body>
<div class="canvas">

  <section class="card card--front" aria-label="Visitkort forside">
    <div class="brand">
      <div class="brand__name"><span class="brand__dot"></span>lumavento</div>
      <div class="brand__rule"></div>
      <p class="brand__tagline">kreativt indhold</p>
    </div>
  </section>

  <section class="card card--back" aria-label="Visitkort bagside">
    <div class="lime-field"></div>

    <div class="contact">
      <p class="contact__name">Mette Larsholm</p>
      <p class="contact__role">Salgsdirektør</p>
      <p class="contact__address">Kastanje Allé 14<br>2100 Nordhavn<br>Tlf. +45 31 20 40 60</p>
      <ul class="contact__list">
        <li><svg viewBox="0 0 16 16"><path d="M3 1l3 3-2 2c1 2 3 4 5 5l2-2 3 3-2 2C6 14 2 10 1 3z"/></svg>+45 31 20 40 60</li>
        <li><svg viewBox="0 0 16 16"><path d="M3 1l3 3-2 2c1 2 3 4 5 5l2-2 3 3-2 2C6 14 2 10 1 3z"/></svg>+45 52 70 80 90</li>
        <li><svg viewBox="0 0 16 16"><path d="M1 3h14v10H1z M1 3l7 6 7-6" fill="none" stroke="#fff" stroke-width="1.6"/></svg>ml@lumavento.dk</li>
        <li><svg viewBox="0 0 16 16"><circle cx="8" cy="8" r="6.5" fill="none" stroke="#fff" stroke-width="1.5"/><path d="M1.5 8h13M8 1.5c-3 3-3 10 0 13M8 1.5c3 3 3 10 0 13" fill="none" stroke="#fff" stroke-width="1.2"/></svg>www.lumavento.dk</li>
      </ul>
    </div>

    <div class="brand">
      <div class="brand__name"><span class="brand__dot"></span>lumavento</div>
      <div class="brand__rule"></div>
      <p class="brand__tagline">kreativt indhold</p>
    </div>
  </section>

</div>
</body>
</html>
```